Post storm repair flyer

looking for an eye catching 6x9 postcard to send out to single family home owners advertising a "Post Storm Repair Special" explaining that after the recent hurricanes its very important to have your roof checked and any repairs fixed right away before they become a bigger more costly problem and that even though your home wasn't directly hit by the storm the high wind gust could've cause unseen damage.
offer $200 off any repair *some rules may apply
Crest Roofing
877.512.DUNE
www.DuneRoofingco.example

```html
<!DOCTYPE html>
<html lang="en">
<head>
<meta charset="utf-8">
<title>Post Storm Repair Special – Crest Roofing Postcard</title>
<link href="https://fonts.googleapis.com/css2?family=Poppins:wght@400;500;600;700;800&family=Great+Vibes&display=swap" rel="stylesheet">
<style>
  :root {
    --stage: #c4c4c4;
    --ink: #050505;
    --gold: #e9b022;
    --white: #ffffff;
    --slate: #3a3a3a;
    --stamp: #ededed;
  }
  * { box-sizing: border-box; margin: 0; padding: 0; }
  html, body { width: 1048px; height: 1200px; overflow: hidden; background: var(--stage); }
  body { position: relative; font-family: "Poppins", sans-serif; color: var(--white); }

  .postcard { position: absolute; left: 163px; width: 723px; height: 482px; overflow: hidden; }
  .postcard--front { top: 96px; background: var(--ink); }
  .postcard--back { top: 622px; background: var(--white); }

  .storm-sky { position: absolute; inset: 0;
    background: radial-gradient(ellipse at 42% 18%, #4a4a4a 0%, #1c1c1c 35%, #050505 70%); }
  .back-panel { position: absolute; left: 0; top: 0; width: 364px; height: 482px; overflow: hidden;
    background: radial-gradient(ellipse at 70% 5%, #3c3c3c 0%, #141414 40%, #050505 75%); }

  .accent-bar { position: absolute; left: 0; width: 3px; background: var(--gold); }

  .site-name { position: absolute; font-weight: 500; letter-spacing: 0.2px; white-space: nowrap; }
  .postcard--front .site-name { left: 48px; top: 116px; font-size: 12px; color: var(--gold); }

  .headline { position: absolute; left: 48px; top: 158px; font-weight: 800; font-size: 44px; line-height: 38px; letter-spacing: -0.5px; white-space: nowrap; }
  .script { position: absolute; font-family: "Great Vibes", cursive; color: var(--gold); }
  .headline-script { left: 46px; top: 222px; font-size: 62px; transform: rotate(-6deg); }

  .check-title { position: absolute; left: 48px; top: 318px; font-weight: 800; font-size: 17px; letter-spacing: 0.2px; }
  .check-copy { position: absolute; left: 48px; top: 340px; width: 150px; font-size: 14px; line-height: 17.5px; color: var(--gold); }

  .phone { position: absolute; display: flex; align-items: center; gap: 6px; font-weight: 700; white-space: nowrap; }
  .phone svg { flex: none; }
  .postcard--front .phone { left: 47px; top: 418px; font-size: 26px; }

  .email-band { position: absolute; background: var(--slate); color: #e6e6e6; font-size: 9.5px;
    display: flex; align-items: center; gap: 5px; white-space: nowrap; }
  .email-band svg { flex: none; }
  .web-band { position: absolute; background: var(--gold); color: var(--ink); font-size: 13px;
    letter-spacing: 1px; display: flex; align-items: center; justify-content: center; white-space: nowrap; }
  .web-band b { font-weight: 700; }
  .postcard--front .email-band { left: 262px; top: 425px; width: 195px; height: 20px; padding-left: 22px;
    clip-path: polygon(0 0, 100% 0, 100% 100%, 8% 100%); }
  .postcard--front .web-band { left: 441px; top: 418px; width: 282px; height: 31px; padding-left: 18px;
    clip-path: polygon(0 0, 100% 0, 100% 100%, 7% 100%); }

  .hex-art { position: absolute; left: 0; top: 0; }

  .offer { position: absolute; width: 120px; text-align: center; color: var(--ink); }
  .offer-label { font-weight: 800; font-size: 14px; color: var(--white); line-height: 16px; }
  .offer-amount { font-weight: 800; font-size: 25px; line-height: 24px; letter-spacing: -0.5px; }
  .offer-amount sup { font-size: 12px; vertical-align: 10px; }
  .offer-amount small { font-size: 13px; }
  .offer-band { margin: 3px auto 0; width: 100px; height: 15px; background: #111; color: var(--white);
    font-weight: 600; font-size: 10px; line-height: 15px; clip-path: polygon(0 0, 100% 0, 93% 100%, 7% 100%); }
  .offer-note { font-size: 6.5px; line-height: 6.5px; margin-top: 3px; }
  .postcard--front .offer { left: 393px; top: 40px; }
  .postcard--back .offer { left: 303px; top: 171px; }

  .back-title { position: absolute; left: 43px; top: 47px; color: var(--gold); font-weight: 800; font-size: 14px; letter-spacing: 0.2px; white-space: nowrap; }
  .back-copy { position: absolute; left: 43px; top: 69px; width: 300px; font-size: 11.3px; line-height: 13.9px; color: #f2f2f2; }
  .process-title { position: absolute; left: 43px; top: 160px; font-weight: 800; font-size: 30px; letter-spacing: -0.3px; white-space: nowrap; }
  .process-script { left: 40px; top: 188px; font-size: 52px; transform: rotate(-4deg); }

  .steps { position: absolute; left: 28px; top: 262px; width: 310px; display: flex; }
  .step { width: 103px; display: flex; flex-direction: column; align-items: center; text-align: center; padding: 0 4px; }
  .step + .step { border-left: 1px solid #555; }
  .step p { margin-top: 8px; font-size: 9.2px; line-height: 11px; color: #f0f0f0; }

  .postcard--back .phone { left: 41px; top: 424px; font-size: 19px; gap: 0; }
  .call-label { font-weight: 500; font-size: 17px; margin-right: 10px; }
  .postcard--back .phone svg { margin-right: 3px; }

  .crew-photo { position: absolute; }
  .crew-photo--standing { left: 367px; top: 328px; width: 108px; height: 154px;
    background: linear-gradient(180deg, rgba(233,176,34,0.55), rgba(40,50,70,0.75));
    clip-path: polygon(20% 0, 45% 0, 60% 30%, 70% 55%, 100% 100%, 35% 100%, 25% 60%, 5% 40%); }
  .crew-photo--roof { left: 219px; top: 420px; width: 160px; height: 62px;
    background: linear-gradient(90deg, rgba(90,90,90,0.7), rgba(230,110,30,0.75) 55%, rgba(120,120,120,0.7));
    clip-path: polygon(0 100%, 35% 30%, 55% 0, 75% 25%, 100% 60%, 100% 100%); }

  .postcard--back .site-name { left: 369px; top: 111px; width: 160px; text-align: center;
    font-size: 9px; color: var(--ink); }
  .stamp-box { position: absolute; left: 614px; top: 41px; width: 64px; height: 78px; background: var(--stamp); }
  .postcard--back .web-band { left: 445px; top: 402px; width: 278px; height: 31px; padding-left: 18px;
    clip-path: polygon(0 0, 100% 0, 100% 100%, 7% 100%); }
  .postcard--back .email-band { left: 518px; top: 434px; width: 205px; height: 17px; padding-left: 24px; font-size: 10px;
    clip-path: polygon(0 0, 100% 0, 100% 100%, 6% 100%); }
</style>
</head>
<body>

<section class="postcard postcard--front" aria-label="Postcard front">
  <div class="storm-sky" role="img" aria-label="Dark stormy night sky with lightning over rooftops"></div>

  <div class="site-name">DUNEROOFINGCO.EXAMPLE</div>

  <h1 class="headline">POST STORM<br>REPAIR</h1>
  <div class="script headline-script">Special</div>

  <div class="accent-bar" style="top:320px;height:69px"></div>
  <h2 class="check-title">CHECK YOUR ROOF</h2>
  <p class="check-copy">Before they become a bigger more costly problem</p>

  <svg class="hex-art" width="723" height="482" viewBox="0 0 723 482">
    <defs>
      <linearGradient id="roofersPhoto" x1="0" y1="0" x2="0" y2="1">
        <stop offset="0" stop-color="#3d4a2a"/>
        <stop offset="0.45" stop-color="#5a6440"/>
        <stop offset="0.7" stop-color="#8a8c8c"/>
        <stop offset="1" stop-color="#6e6256"/>
      </linearGradient>
      <linearGradient id="lightningPhoto" x1="0" y1="0" x2="0" y2="1">
        <stop offset="0" stop-color="#6d4a78"/>
        <stop offset="0.6" stop-color="#8a6a92"/>
        <stop offset="1" stop-color="#3a2e38"/>
      </linearGradient>
    </defs>
    <polygon points="526,40 678.4,128 678.4,304 526,392 373.6,304 373.6,128" fill="#ffffff"/>
    <polygon points="526,58 662.8,137 662.8,295 526,374 389.2,295 389.2,137" fill="url(#roofersPhoto)" role="img" aria-label="Two roofers in hard hats repairing a shingle roof"/>
    <polygon points="384,185 475.8,238 475.8,344 384,397 292.2,344 292.2,238" fill="#e9b022"/>
    <polygon points="384,214 450.7,252.5 450.7,329.5 384,368 317.3,329.5 317.3,252.5" fill="#ffffff"/>
    <polygon points="384,226 440.3,258.5 440.3,323.5 384,356 327.7,323.5 327.7,258.5" fill="url(#lightningPhoto)" role="img" aria-label="Lightning strike over a tiled roof at dusk"/>
    <polygon points="453,23 505,53 505,113 453,143 401,113 401,53" fill="#e9b022"/>
  </svg>

  <div class="offer">
    <div class="offer-label">OFFER</div>
    <div class="offer-amount"><sup>$</sup>200<small>OFF</small></div>
    <div class="offer-band">ANY REPAIR</div>
    <div class="offer-note">*some rules may<br>apply</div>
  </div>

  <div class="phone">
    <svg width="20" height="20" viewBox="0 0 20 20"><circle cx="10" cy="10" r="10" fill="#e9b022"/><path d="M7 5.5l2 2-1 1.3c.6 1.3 1.6 2.3 2.9 2.9l1.3-1 2 2-1.2 1.5c-3.5-.3-6.6-3.4-6.9-6.9z" fill="#050505"/></svg>
    877.512.DUNE
  </div>

  <div class="email-band">
    <svg width="11" height="8" viewBox="0 0 11 8"><rect width="11" height="8" fill="#e9b022"/><path d="M0 0l5.5 4.5L11 0" stroke="#3a3a3a" fill="none"/></svg>
    info@duneroofingco.example
  </div>
  <div class="web-band">www.<b>DuneRoofingco</b>.example</div>
</section>

<section class="postcard postcard--back" aria-label="Postcard back">
  <div class="back-panel" role="img" aria-label="Dark storm clouds with faint lightning"></div>

  <div class="accent-bar" style="top:46px;height:98px"></div>
  <h2 class="back-title">AFTER THE RECENT HURRICANES</h2>
  <p class="back-copy">its very important to have your roof checked and any repairs fixed right away before they become a bigger more costly problem and that even though your home wasn't directly hit by the storm the high wind gust could've cause unseen damage.</p>

  <h2 class="process-title">CREST ROOFING</h2>
  <div class="script process-script">Process</div>

  <div class="steps">
    <div class="step">
      <svg width="40" height="44" viewBox="0 0 40 44"><polygon points="20,1 38,11.5 38,32.5 20,43 2,32.5 2,11.5" fill="none" stroke="#777" stroke-dasharray="2 2"/><circle cx="16" cy="17" r="3.5" fill="#e9b022"/><circle cx="24" cy="17" r="3.5" fill="#e9b022"/><path d="M10 29c0-5 3-7 6-7s6 2 6 7zM18 29c0-5 3-7 6-7s6 2 6 7z" fill="#e9b022"/></svg>
      <p>Complimentary consultation to access your roofing needs and review our honest recommendations</p>
    </div>
    <div class="step">
      <svg width="40" height="44" viewBox="0 0 40 44"><polygon points="20,1 38,11.5 38,32.5 20,43 2,32.5 2,11.5" fill="none" stroke="#777" stroke-dasharray="2 2"/><path d="M9 30l22-9v9z" fill="#e9b022"/><circle cx="17" cy="15" r="3" fill="#e9b022"/><path d="M14 19h6l2 5-3 1-2-3-3 3z" fill="#e9b022"/></svg>
      <p>Our team of professionals replace, restore, or repair your roof making the process as stress-free as possible.</p>
    </div>
    <div class="step">
      <svg width="40" height="44" viewBox="0 0 40 44"><polygon points="20,1 38,11.5 38,32.5 20,43 2,32.5 2,11.5" fill="none" stroke="#777" stroke-dasharray="2 2"/><circle cx="20" cy="19" r="8" fill="none" stroke="#e9b022" stroke-width="2.5"/><circle cx="20" cy="19" r="4" fill="#e9b022"/><path d="M15 26l-2 7 4-2 3 3 0-7zM25 26l2 7-4-2-3 3z" fill="#e9b022"/></svg>
      <p>100% satisfaction, peace of mind, &amp; continued professional coverage backed by Crest Protection</p>
    </div>
  </div>

  <div class="crew-photo crew-photo--roof" role="img" aria-label="Roofer in orange safety gear kneeling on a tiled roof"></div>
  <div class="crew-photo crew-photo--standing" role="img" aria-label="Roofer in hard hat and safety vest walking across a roof"></div>

  <svg class="hex-art" width="723" height="482" viewBox="0 0 723 482">
    <polygon points="363,137 421,170.5 421,237.5 363,271 305,237.5 305,170.5" fill="#e9b022"/>
  </svg>
  <div class="offer">
    <div class="offer-label">OFFER</div>
    <div class="offer-amount"><sup>$</sup>200<small>OFF</small></div>
    <div class="offer-band">ANY REPAIR</div>
    <div class="offer-note">*some rules may<br>apply</div>
  </div>

  <div class="phone">
    <span class="call-label">CALL US</span>
    <svg width="16" height="16" viewBox="0 0 20 20"><circle cx="10" cy="10" r="10" fill="#e9b022"/><path d="M7 5.5l2 2-1 1.3c.6 1.3 1.6 2.3 2.9 2.9l1.3-1 2 2-1.2 1.5c-3.5-.3-6.6-3.4-6.9-6.9z" fill="#050505"/></svg>
    877.512.DUNE
  </div>

  <div class="site-name">DUNEROOFINGCO.EXAMPLE</div>
  <div class="stamp-box" aria-label="Postage area"></div>

  <div class="web-band">www.<b>DuneRoofingco</b>.example</div>
  <div class="email-band">
    <svg width="11" height="8" viewBox="0 0 11 8"><rect width="11" height="8" fill="#e9b022"/><path d="M0 0l5.5 4.5L11 0" stroke="#3a3a3a" fill="none"/></svg>
    info@duneroofingco.example
  </div>
</section>

</body>
</html>
```